Animation College website

Name of College: Brightloom Academy of 3D Animation and VFX

We need a redesigned modern website for Brightloom. The web-design should communicate a VFX and animation school and education. We will also need full access to the website once completed. We will also need access to the website to be able to make changes to the content and site ideally the website would be built on Wordpress.

To learn more about what the College please visit: http://brightloom-academy.example/
The video on the homepage demonstrates why Brightloom is a unique college offering 3D animation and VFX. The direct link to the video can be watched here: https://videohost.example/482915036

Client Profile Summary: Brightloom is an improved concept in job skills training for the 3D animation and visual effects industries. Our high graduate job placement numbers are based on the assertion that job skills must include more than simply learning to use software tools. Where nearly every digital media program teaches tools, job skills training should be about learning how to do a job in addition to learning how to use software tools. Brightloom is taught in an apprenticeship style with very experienced faculty mentoring and teaching students to learn how to master their craft (VFX and animation) so they can seamlessly step into industry and excel.

Target Market(s)

High school students, students interested in learning about animation and 3D.

Industry/Entity Type

College

Coding

Coded - Design and coding required

Number of Pages Required

5+ page

Font styles to use
Sans Serif

Colors

Designer to choose colors to be used in the design.

Requirements
Must have
• Please include the video on the current Brightloom-academy.example website. https://videohost.example/482915036
• Use the same content on the current brightloom-academy.example website.
• Include a page to showcase student work.
• Website must also be mobile responsive.
Should not have
• The attached PDF of the landing page is just an example of something we like. You do not have to replicate this. The PDF landing page is showing the colour blue you should incorporate.

```html
<!DOCTYPE html>
<html lang="en">
<head>
<meta charset="utf-8">
<title>Brightloom Academy of 3D Animation and VFX</title>
<link rel="stylesheet" href="https://fonts.googleapis.com/css2?family=Montserrat:wght@300;400;600;700&family=Open+Sans:wght@400;600;700&display=swap">
<style>
:root{
  --blue:#1a6fb3;
  --blue-band:#14769f;
  --blue-line:#1565c0;
  --ink:#3d3d3d;
  --body:#666;
  --white:#fff;
  --footer:#262626;
  --hero-a:#1c2530;
  --hero-b:#3a4a58;
  --panel:rgba(30,30,30,.72);
  --badge-a:#1d3e73;
  --badge-b:#e6eef7;
  --badge-c:#c9d3dd;
  --badge-d:#e87722;
  --badge-e:#d9b23a;
}
*{box-sizing:border-box;margin:0;padding:0}
html,body{width:1200px;height:2707px;overflow:hidden;background:var(--white)}
body{position:relative;font-family:"Open Sans",Arial,sans-serif;color:var(--body)}
.abs{position:absolute}
.center{left:0;width:1200px;text-align:center}

/* hero */
.hero{position:absolute;left:0;top:0;width:1200px;height:646px;
  background:linear-gradient(120deg,var(--hero-a) 0%,#2b3947 35%,var(--hero-b) 60%,#20262c 100%);
  border-top:6px solid var(--blue-line)}
.brand{position:absolute;left:99px;top:22px;display:flex;align-items:center;gap:12px}
.brand-mark{width:52px;height:52px;border-radius:50%;background:var(--white)}
.brand-name{font-family:Montserrat,sans-serif;font-weight:700;font-size:24px;color:var(--white);line-height:1}
.brand-tag{font-family:Montserrat,sans-serif;font-weight:600;font-size:11px;color:var(--white);margin-top:6px;letter-spacing:.3px}
.menu{position:absolute;left:1083px;top:28px}
.hero-title{position:absolute;left:99px;top:308px;width:600px;font-family:Montserrat,sans-serif;font-weight:700;font-size:32px;line-height:46px;color:var(--white);letter-spacing:.5px}
.hero-sub{position:absolute;left:99px;top:422px;font-family:Montserrat,sans-serif;font-weight:600;font-size:19px;color:var(--white)}
.form{position:absolute;left:691px;top:135px;width:379px;height:505px;background:var(--panel)}
.form h2{position:absolute;left:0;top:14px;width:379px;text-align:center;font-family:Montserrat,sans-serif;font-weight:600;font-size:22px;color:var(--white);letter-spacing:.5px}
.form p{position:absolute;left:0;top:58px;width:379px;text-align:center;font-weight:700;font-size:14px;line-height:20px;color:var(--white)}
.field{position:absolute;left:47px;width:293px;height:27px;border:1px solid rgba(255,255,255,.75);font-size:10px;color:#ccc;padding:6px 6px}
.field.tall{height:58px}
.send{position:absolute;left:67px;top:397px;width:253px;height:37px;background:var(--blue);color:var(--white);font-family:Montserrat,sans-serif;font-weight:600;font-size:16px;text-align:center;line-height:37px;letter-spacing:.5px}

/* badges */
.badges{position:absolute;left:0;top:646px;width:1200px;height:139px;border-bottom:5px solid var(--blue-line)}
.badge{position:absolute;top:20px;width:99px;height:99px}
.badge.round{border-radius:50%}

/* text sections */
h1,h3{font-family:Montserrat,sans-serif}
.sec-title{font-weight:600;font-size:31px;color:var(--ink)}
.sec-sub{font-family:Montserrat,sans-serif;font-weight:600;font-size:16px;color:var(--blue);letter-spacing:.3px}
.copy{font-size:11.5px;line-height:20px;color:var(--body)}
.copy-strong{font-weight:700;font-size:13px;line-height:20px;color:var(--ink)}
.wide{left:95px;width:1010px;text-align:center}

/* video */
.video{position:absolute;left:0;top:1029px;width:1200px;height:397px;background:linear-gradient(90deg,#2b2018 0%,#4a3a2c 30%,#5a4a3c 60%,#8a2a1e 80%,#2a2a2a 100%)}
.video-word{position:absolute;left:735px;top:38px;font-family:Montserrat,sans-serif;font-weight:300;font-size:50px;color:var(--white);letter-spacing:1px}
.video-tools{position:absolute;left:1128px;top:24px;width:26px}
.controls{position:absolute;left:202px;top:352px;width:800px;height:28px;background:rgba(20,20,20,.75)}

/* testimonial */
.testimonial{position:absolute;left:0;top:1762px;width:1200px;height:397px;background:linear-gradient(90deg,#1e2a38,#2f4a66 50%,#1e2a38)}
.quote-box{position:absolute;left:283px;top:75px;width:632px;height:269px;background:rgba(26,111,179,.82)}
.quote-frame{position:absolute;left:13px;top:13px;width:606px;height:243px;border:1px solid rgba(255,255,255,.8)}
.avatar{position:absolute;left:551px;top:71px;width:100px;height:100px;border-radius:50%;background:linear-gradient(#b89878,#5a4030);border:3px solid var(--white)}
.quote{position:absolute;left:40px;top:100px;width:552px;text-align:center;font-weight:600;font-size:14px;line-height:20px;color:var(--white)}
.quote-name{position:absolute;left:0;top:218px;width:632px;text-align:center;font-family:Montserrat,sans-serif;font-weight:700;font-size:16px;color:var(--white)}

/* cta + footer */
.cta{position:absolute;left:0;top:2487px;width:1200px;height:112px;background:var(--blue-band);text-align:center;font-family:Montserrat,sans-serif;font-weight:400;font-size:25px;line-height:39px;color:var(--white);padding-top:17px}
.footer{position:absolute;left:0;top:2599px;width:1200px;height:108px;background:var(--footer)}
.social{position:absolute;left:493px;top:24px;display:flex;gap:12px}
.social span{width:26px;height:26px;border-radius:50%;border:2px solid #ddd}
.legal{position:absolute;left:0;top:72px;width:1200px;text-align:center;font-weight:600;font-size:11px;color:#ddd}
</style>
</head>
<body>

<header class="hero" role="img" aria-label="Students working at computer workstations in an animation studio">
  <div class="brand">
    <div class="brand-mark"></div>
    <div>
      <div class="brand-name">Brightloom</div>
      <div class="brand-tag">GET SKILLS, GOT GRADES</div>
    </div>
  </div>
  <svg class="menu" width="20" height="18" viewBox="0 0 20 18"><rect y="1" width="20" height="3" fill="#fff"/><rect y="7.5" width="20" height="3" fill="#fff"/><rect y="14" width="20" height="3" fill="#fff"/></svg>
  <h1 class="hero-title">3D Animation &amp; VFX One - Year Intensive Training Program</h1>
  <div class="hero-sub">Train Alongside Passionate &amp; Experienced Industry Masters</div>

  <form class="form">
    <h2>WANT TO KNOW MORE?</h2>
    <p>Complete this form to receive more<br>information about program details &amp; more!</p>
    <div class="field" style="top:118px">First Name *</div>
    <div class="field" style="top:157px">Last Name *</div>
    <div class="field" style="top:197px">Phone *</div>
    <div class="field" style="top:237px">Email *</div>
    <div class="field" style="top:277px">Country Of Residence *</div>
    <div class="field tall" style="top:318px">Comments</div>
    <div class="send">SEND ME FREE INFO</div>
  </form>
</header>

<section class="badges" aria-label="Accreditation badges">
  <div class="badge round" style="left:97px;background:var(--badge-a)"></div>
  <div class="badge round" style="left:330px;background:var(--badge-b);border:4px solid var(--badge-a)"></div>
  <div class="badge round" style="left:551px;background:var(--badge-c)"></div>
  <div class="badge" style="left:787px;width:80px;background:var(--badge-d)"></div>
  <div class="badge" style="left:1000px;background:var(--badge-e)"></div>
</section>

<section>
  <h3 class="abs center sec-title" style="top:828px">One-Year Intensive Training Program</h3>
  <div class="abs center sec-sub" style="top:880px">An exciting, comprehensive program with a toss graduate employment rate.</div>
  <p class="abs copy wide" style="top:920px">The 48-week Brightloom One-Year Intensive Training Program is designed to provide students the practical skills and real-world experience needed to thrive in the film and Tv animation, and VFX industries. Students are mentored by our passionate instructors who have extensive industry experience. Each of our instructors knows exactly what it takes for students to be successful. We carefully crafted the program curriculum to teach students how to function in a real production team so that they can be highly-effective professionals once they enter the workforce.</p>
</section>

<section class="video" role="img" aria-label="Program video featuring a graduate speaking about the school">
  <div class="video-word">Phenomenal</div>
  <svg class="video-tools" width="26" height="130" viewBox="0 0 26 130" fill="none" stroke="#fff" stroke-width="2">
    <path d="M13 18 L5 10 a4 4 0 0 1 8-4 a4 4 0 0 1 8 4z" fill="#fff"/>
    <circle cx="13" cy="44" r="8"/><path d="M13 39v5h4"/>
    <path d="M5 72l8-4 8 4-8 4z M5 77l8 4 8-4 M5 82l8 4 8-4"/>
    <path d="M4 110l18-8-6 18-3-7z" fill="#fff"/>
  </svg>
  <div class="controls">
    <svg width="800" height="28" viewBox="0 0 800 28">
      <path d="M14 8l12 6-12 6z" fill="#fff"/>
      <rect x="40" y="13" width="600" height="8" fill="#555"/>
      <rect x="40" y="13" width="180" height="8" fill="#777"/>
      <text x="42" y="10" font-size="8" fill="#fff" font-family="Open Sans,sans-serif">02:07</text>
      <rect x="718" y="16" width="2" height="4" fill="#1a9fd8"/><rect x="722" y="13" width="2" height="7" fill="#1a9fd8"/><rect x="726" y="10" width="2" height="10" fill="#1a9fd8"/><rect x="730" y="8" width="2" height="12" fill="#fff"/>
      <text x="742" y="19" font-size="11" font-weight="700" fill="#fff" font-family="Open Sans,sans-serif">HD</text>
      <path d="M770 8l6 6M776 8l-6 6M770 20l6-6" stroke="#fff" stroke-width="2"/>
    </svg>
  </div>
</section>

<section>
  <h3 class="abs center sec-title" style="top:1469px">Learn Animation &amp; Visual Effects Production from the Experts</h3>
  <div class="abs center sec-sub" style="top:1516px">The world's first and sole simulated production training program</div>
  <p class="abs copy wide" style="top:1556px">Our philosophy is unique. We don't focus on grades. Instead, we focus on preparing each of our students for the challenges of working as 3D artists such as animators, lighting TDs, riggers, modellers, compositors and more. Our instructors teach you until you're confident in your skills. If you need more help, we train you until you're ready.</p>
  <p class="abs center copy-strong" style="top:1622px">Students grasp valuable skills that employers are looking for over the course of three intensive terms:</p>
  <p class="abs center copy" style="top:1664px">Core Skills: An intensive introduction to skills involving cameras, modeling, animation, dynamics, lighting, composition, production, and more.<br>Transition into Practice: Expand on core skills with advanced training and team production.<br>Practical Training: Practical hands-on production and dailies training.</p>
</section>

<section class="testimonial" role="img" aria-label="Students in a computer lab working on animation shots">
  <div class="quote-box">
    <div class="quote-frame"></div>
    <p class="quote">"I was able to get my 1st job only two weeks after finishing this program. It is the future of VFX training. Brightloom has changed my life and changed the way that I think about the world around me. I would highly recommend this program above any other, to anyone wishing to pursue a career in the film industry."</p>
    <div class="quote-name">Dana Whitfield, Lighting Artist, Northgate FX</div>
  </div>
  <div class="avatar" role="img" aria-label="Portrait of the graduate"></div>
</section>

<section>
  <h3 class="abs center sec-title" style="top:2195px">The Brightloom Advantage</h3>
  <div class="abs center sec-sub" style="top:2246px">A Program Designed By Industry, For Industry</div>
  <p class="abs copy wide" style="top:2285px">There's a reason why each of our graduates have found work in their field. We don't sell courses, we provide relevant training. In order to bring out the best in our students, we run a program that we know will maximize each student's potential.</p>
  <p class="abs center copy-strong" style="top:2353px">Brightloom offers an un-paralleled training experience. Here are a few examples of what makes our school unique:<br>Affordable tuition for both domestic and international students</p>
  <p class="abs center copy" style="top:2418px">A faculty of 12 world-class industry masters, A Maximum class size of 12 students, A One-on-one mentorship<br>A Employment opportunities, A Scholarships, And more!</p>
</section>

<section class="cta">Want To Learn More?<br>Fill Out The Form Above To Receive Information About The Program!</section>

<footer class="footer">
  <div class="social"><span></span><span></span><span></span><span></span><span></span><span></span></div>
  <p class="legal">© Copyright 2017 Brightloom Academy of 3D Animation and VFX. All Rights Reserved. Privacy Policy.</p>
</footer>

</body>
</html>
```